School Hallway Magnetic Display Design for school values

I am looking for a someone to help me design a magnetic hallway display that will hang in the hallway of our small school. There are several elements, including 1. 6ft by 4ft designed magnetic bulletin board, 2. Magnets that will stick to the board. See attachment for which elements belong where. The display will be for our MOBLAT program, which rewards students for demonstrating our school values. We want the display to be beautiful and interactive. We are also rebranding, so we want the design to align with our new fonts and colors. In the attached PDF is an outline of our new brand guidelines. Unfortunately, we don't have the color codes, but I'm hoping that you can match the colors listed. Attached are elements to be used on the board, but please use your creativity to make it more dynamic and visually appealing. For example, the star magnets could be another shape. The MOBLAT magnets must remain the same. I've included two photos of boards at other schools that inspired this project.

Target Market(s)

School Community

Industry/Entity Type

Education

Requirements
Should not have
• School Logo

```html
<!DOCTYPE html>
<html lang="en">
<head>
<meta charset="UTF-8">
<title>MOBLAT of the Month Board</title>
<link href="https://fonts.googleapis.com/css2?family=Abril+Fatface&display=swap" rel="stylesheet">
<style>
  :root {
    --navy: #1f4e74;
    --badge-ring: #2b4f8f;
    --cream: #fbf1d6;
    --ink: #111111;
    --white: #ffffff;
    --sky: #a9c9e6;
    --sun: #fcd77a;
    --lilac: #b99ac6;
    --sage: #d6e0b8;
    --coral: #e0826b;
    --star: #fcdc7a;
    --stage: #979797;
  }
  * { margin: 0; padding: 0; box-sizing: border-box; }
  html, body { width: 1200px; height: 888px; overflow: hidden; background: var(--stage); }
  .board {
    position: absolute; left: 0; top: 44px; width: 1200px; height: 800px;
    font-family: "Abril Fatface", serif;
  }
  .board-pattern {
    position: absolute; inset: 0;
    background: linear-gradient(120deg, var(--navy) 0%, var(--sun) 25%, var(--sky) 50%, var(--lilac) 70%, var(--coral) 85%, var(--navy) 100%);
  }
  .board-panel {
    position: absolute; left: 35px; top: 30px; width: 1137px; height: 744px;
    background: var(--white); border: 1.5px solid var(--ink); border-radius: 30px;
  }
  .title-bar {
    position: absolute; left: 58px; top: 80px; width: 803px; height: 92px;
    background: var(--navy); border-radius: 10px;
    color: var(--cream); font-size: 66px; letter-spacing: 1px; line-height: 92px;
    text-align: center; white-space: nowrap;
  }
  .value {
    position: absolute; width: 240px; text-align: center;
  }
  .value-badge {
    display: block; margin: 0 auto; width: 140px; height: 140px;
  }
  .value-name {
    display: block; margin-top: 16px; font-size: 27px; color: var(--ink); letter-spacing: 0.5px;
  }
  .star-row { position: absolute; left: 212px; top: 624px; }
  .thermometer { position: absolute; left: 930px; top: 80px; }
</style>
</head>
<body>
<main class="board">
  <div class="board-pattern" role="img" aria-label="Geometric tile pattern of half circles and stripes in navy, yellow, blue and lilac"></div>
  <div class="board-panel"></div>

  <h1 class="title-bar">MOBLAT OF THE MONTH</h1>

  <div class="value" style="left:92px; top:214px;">
    <svg class="value-badge" viewBox="0 0 140 140"><circle cx="70" cy="70" r="68" fill="var(--badge-ring)"/><circle cx="70" cy="70" r="52" fill="var(--sky)" role="img" aria-label="Simplicity icon"/></svg>
    <span class="value-name">SIMPLICITY</span>
  </div>
  <div class="value" style="left:331px; top:214px;">
    <svg class="value-badge" viewBox="0 0 140 140"><circle cx="70" cy="70" r="68" fill="var(--badge-ring)"/><circle cx="70" cy="70" r="52" fill="var(--sun)" role="img" aria-label="Peace icon"/></svg>
    <span class="value-name">PEACE</span>
  </div>
  <div class="value" style="left:562px; top:214px;">
    <svg class="value-badge" viewBox="0 0 140 140"><circle cx="70" cy="70" r="68" fill="var(--badge-ring)"/><circle cx="70" cy="70" r="52" fill="var(--lilac)" role="img" aria-label="Integrity icon"/></svg>
    <span class="value-name">INTEGRITY</span>
  </div>
  <div class="value" style="left:92px; top:413px;">
    <svg class="value-badge" viewBox="0 0 140 140"><circle cx="70" cy="70" r="68" fill="var(--badge-ring)"/><circle cx="70" cy="70" r="52" fill="var(--sage)" role="img" aria-label="Community icon"/></svg>
    <span class="value-name">COMMUNITY</span>
  </div>
  <div class="value" style="left:331px; top:413px;">
    <svg class="value-badge" viewBox="0 0 140 140"><circle cx="70" cy="70" r="68" fill="var(--badge-ring)"/><circle cx="70" cy="70" r="52" fill="var(--coral)" role="img" aria-label="Equality icon"/></svg>
    <span class="value-name">EQUALITY</span>
  </div>
  <div class="value" style="left:562px; top:413px;">
    <svg class="value-badge" viewBox="0 0 140 140"><circle cx="70" cy="70" r="68" fill="var(--badge-ring)"/><circle cx="70" cy="70" r="52" fill="var(--white)" role="img" aria-label="Stewardship icon"/></svg>
    <span class="value-name">STEWARDSHIP</span>
  </div>

  <svg class="star-row" width="490" height="72" viewBox="0 0 490 72" aria-label="Six reward stars">
    <defs>
      <polygon id="star" points="36,1 45,24 71,26 51,42 57,68 36,54 15,68 21,42 1,26 27,24" fill="var(--star)"/>
    </defs>
    <use href="#star" x="0"/><use href="#star" x="82"/><use href="#star" x="164"/>
    <use href="#star" x="246"/><use href="#star" x="328"/><use href="#star" x="410"/>
  </svg>

  <svg class="thermometer" width="210" height="600" viewBox="0 0 210 600" aria-label="Progress thermometer">
    <g stroke="var(--ink)" stroke-width="2">
      <line x1="13" y1="72" x2="66" y2="72"/><line x1="36" y1="80" x2="66" y2="80"/>
      <line x1="13" y1="88" x2="66" y2="88"/><line x1="36" y1="96" x2="66" y2="96"/>
      <line x1="13" y1="104" x2="66" y2="104"/><line x1="36" y1="112" x2="66" y2="112"/>
      <line x1="13" y1="120" x2="66" y2="120"/><line x1="36" y1="128" x2="66" y2="128"/>
      <line x1="13" y1="136" x2="66" y2="136"/><line x1="36" y1="144" x2="66" y2="144"/>
      <line x1="13" y1="152" x2="66" y2="152"/><line x1="36" y1="160" x2="66" y2="160"/>
      <line x1="13" y1="168" x2="66" y2="168"/><line x1="36" y1="176" x2="66" y2="176"/>
      <line x1="13" y1="184" x2="66" y2="184"/><line x1="36" y1="192" x2="66" y2="192"/>
      <line x1="13" y1="200" x2="66" y2="200"/><line x1="36" y1="208" x2="66" y2="208"/>
      <line x1="13" y1="216" x2="66" y2="216"/><line x1="36" y1="224" x2="66" y2="224"/>
      <line x1="13" y1="232" x2="66" y2="232"/><line x1="36" y1="240" x2="66" y2="240"/>
      <line x1="13" y1="248" x2="66" y2="248"/><line x1="36" y1="256" x2="66" y2="256"/>
      <line x1="13" y1="264" x2="66" y2="264"/><line x1="36" y1="272" x2="66" y2="272"/>
      <line x1="13" y1="280" x2="66" y2="280"/><line x1="36" y1="288" x2="66" y2="288"/>
      <line x1="13" y1="296" x2="66" y2="296"/><line x1="36" y1="304" x2="66" y2="304"/>
      <line x1="13" y1="312" x2="66" y2="312"/><line x1="36" y1="320" x2="66" y2="320"/>
      <line x1="13" y1="328" x2="66" y2="328"/><line x1="36" y1="336" x2="66" y2="336"/>
      <line x1="13" y1="344" x2="66" y2="344"/><line x1="36" y1="352" x2="66" y2="352"/>
      <line x1="13" y1="360" x2="66" y2="360"/><line x1="36" y1="368" x2="66" y2="368"/>
      <line x1="13" y1="376" x2="66" y2="376"/><line x1="36" y1="384" x2="66" y2="384"/>
    </g>
    <path d="M74 430 V40 A33.5 33.5 0 0 1 141 40 V430 A81 81 0 1 1 74 430 Z" fill="var(--white)" stroke="var(--ink)" stroke-width="2"/>
    <ellipse cx="127" cy="526" rx="12" ry="16" transform="rotate(20 127 526)" fill="var(--ink)"/>
  </svg>
</main>
</body>
</html>
```